The Quiet Lantern Business Card

I need a business card designed for The Quiet Lantern. The company provides on site support and education to end consumers in the ins and outs of all our digital devices. We advise on product purchase, installation, maintenance and troubleshooting. Anything from cordless phones to home networks.
My initial concept is double sided with the white logo on green on one side and contact details and a small logo on the flip side (logo package attached)
Contact Details:
Pablo Strand
Managing Director
PO Box 4
Marlow Heights, NSW 2091
Phone: 0438 559 106
email: pablo@quietlantern.com.au
web: www.quietlantern.com.au
Target Market(s)
Busy professionals and retired folks.
Industry/Entity Type
Education
Look and feel

```html
<!DOCTYPE html>
<html lang="en">
<head>
<meta charset="utf-8">
<title>The Quiet Lantern – Business Card</title>
<link href="https://fonts.googleapis.com/css2?family=Exo+2:wght@300;400;600;700&display=swap" rel="stylesheet">
<style>
  :root {
    --backdrop: #e8e8e4;
    --card: #ffffff;
    --green: #7cb82f;
    --navy: #143248;
    --ink: #1d2e3c;
  }
  * { box-sizing: border-box; margin: 0; padding: 0; }
  html, body { width: 1200px; height: 897px; overflow: hidden; }
  body {
    background: var(--backdrop);
    font-family: "Exo 2", Arial, sans-serif;
    color: var(--ink);
    position: relative;
  }
  .card {
    position: absolute;
    top: 288px;
    width: 540px;
    height: 320px;
    background: var(--card);
    border-radius: 30px;
    overflow: hidden;
    box-shadow: 0 6px 18px rgba(0,0,0,0.18);
  }
  .card--front { left: 40px; }
  .card--back { left: 620px; }
  .card__frame {
    position: absolute;
    inset: 13px;
    border: 3px solid var(--green);
    border-radius: 22px;
  }
  .front__band {
    position: absolute;
    left: 0; top: 40px;
    width: 228px; height: 42px;
    background: var(--navy);
    border-radius: 0 21px 21px 0;
  }
  .front__tab {
    position: absolute;
    left: 478px; top: 0;
    width: 40px; height: 92px;
    background: var(--navy);
    border-radius: 0 0 20px 20px;
  }
  .front__identity {
    position: absolute;
    left: 248px; top: 44px;
    color: var(--navy);
  }
  .front__name {
    font-weight: 700;
    font-size: 21px;
    letter-spacing: 0.5px;
    line-height: 1.1;
  }
  .front__role {
    font-weight: 600;
    font-size: 11.5px;
    letter-spacing: 0.6px;
  }
  .brand {
    display: flex;
    align-items: center;
    gap: 10px;
  }
  .brand__dot {
    border-radius: 50%;
    background: var(--green);
    flex: none;
  }
  .brand__name {
    font-weight: 300;
    color: var(--navy);
    white-space: nowrap;
  }
  .front__brand {
    position: absolute;
    left: 300px; top: 150px;
  }
  .front__brand .brand__dot { width: 26px; height: 26px; }
  .front__brand .brand__name { font-size: 22px; }
  .front__contact {
    position: absolute;
    left: 40px; top: 190px;
    font-size: 11.5px;
    line-height: 1.45;
  }
  .front__address { font-weight: 600; font-size: 12.5px; margin-bottom: 6px; }
  .contact-line {
    display: flex;
    align-items: center;
    gap: 7px;
    font-size: 11px;
  }
  .contact-line svg { width: 10px; height: 10px; fill: var(--navy); flex: none; }
  .back__brand {
    position: absolute;
    left: 0; right: 0; top: 0; bottom: 0;
    justify-content: center;
    gap: 14px;
  }
  .back__brand .brand__dot { width: 44px; height: 44px; }
  .back__brand .brand__name { font-size: 38px; }
</style>
</head>
<body>

<section class="card card--front">
  <div class="card__frame"></div>
  <div class="front__band"></div>
  <div class="front__tab"></div>

  <div class="front__identity">
    <p class="front__name">PABLO STRAND</p>
    <p class="front__role">GENERAL MANAGER</p>
  </div>

  <div class="brand front__brand">
    <span class="brand__dot"></span>
    <span class="brand__name">The Quiet Lantern</span>
  </div>

  <div class="front__contact">
    <p class="front__address">PO Box 4,<br>Marlow Heights, NSW 2091</p>
    <p class="contact-line">
      <svg viewBox="0 0 10 10" aria-hidden="true"><path d="M2 0.5 L3.8 2.6 L2.9 3.6 Q4 6 6.4 7.1 L7.4 6.2 L9.5 8 L8.3 9.5 Q2 8.5 0.5 1.7 Z"/></svg>
      <span>0438 559 106</span>
    </p>
    <p class="contact-line">
      <svg viewBox="0 0 10 10" aria-hidden="true"><path d="M2.5 0 H7.5 V10 H2.5 Z M3.4 1 V8 H6.6 V1 Z"/></svg>
      <span>0438 559 106</span>
    </p>
    <p class="contact-line">
      <svg viewBox="0 0 10 10" aria-hidden="true"><path d="M0 2 H10 V8.5 H0 Z M0.8 2.6 L5 5.6 L9.2 2.6 Z" fill-rule="evenodd"/></svg>
      <span>pablo@quietlantern.com.au</span>
    </p>
    <p class="contact-line">
      <svg viewBox="0 0 10 10" aria-hidden="true"><circle cx="5" cy="5" r="4.6"/><path d="M0.5 5 H9.5 M5 0.5 V9.5" stroke="#fff" stroke-width="0.7"/></svg>
      <span>www.quietlantern.com.au</span>
    </p>
  </div>
</section>

<section class="card card--back">
  <div class="card__frame"></div>
  <div class="brand back__brand">
    <span class="brand__dot"></span>
    <span class="brand__name">The Quiet Lantern</span>
  </div>
</section>

</body>
</html>
```